Local Flower Farm Needs Business Card Design

I need business cards designed for a flower farm based in Eudora, Kansas.
Business Info:
We are a local cut flower farm located in Eudora, Kansas, founded by Corinne Haldwick. What started as a passion for agriculture and search for more joy in daily life has blossomed into a small business dedicated to providing the community with beautiful, fresh, and sustainable flowers. We specialize in local, seasonal blooms, ensuring that every petal reflects the care and dedication we pour into our craft. Our mission is to deliver the highest quality flowers directly to our customers through local farmers markets and to florists who share our commitment to sustainability. Join us in celebrating the beauty of nature, one bloom at a time!
Contact Details:
Corinne Haldwick
Owner
Phone 913-555-0147
Facebook: Rosalind Thorpe Gardens
Instagram: @RosalindThorpeGardens
Website: RosalindThorpeGardens.example
Target Market(s)
Wholesale to Florists and Direct to Consumer via Farmers Market
Industry/Entity Type
Florist, Farm
Contact Information for Business Card
Name, Contact Info, Logo
Look and feel
Each slider illustrates characteristics of the customer's brand and the style your logo design should communicate.

```html
<!DOCTYPE html>
<html lang="en">
<head>
<meta charset="utf-8">
<title>Rosalind Thorpe Gardens – Business Cards</title>
<link rel="stylesheet" href="https://fonts.googleapis.com/css2?family=Crimson+Text:wght@400;700&display=swap">
<style>
  :root {
    --ink: #0b262b;
    --paper: #ffffff;
    --silver: #c5c8cb;
    --backdrop: #e8e8e8;
    --text-font: "Crimson Text", Georgia, serif;
  }
  * { margin: 0; padding: 0; box-sizing: border-box; }
  html, body {
    width: 1200px;
    height: 900px;
    overflow: hidden;
    background: var(--backdrop);
    font-family: var(--text-font);
  }
  .sheet {
    position: relative;
    width: 1200px;
    height: 900px;
  }
  .card {
    position: absolute;
    left: 250px;
    width: 700px;
    height: 400px;
    overflow: hidden;
  }
  .card--front { top: 30px; background: var(--ink); }
  .card--back { top: 470px; background: var(--paper); }

  .brand-seal {
    position: absolute;
    z-index: 2;
    border-radius: 50%;
    display: flex;
    align-items: center;
    justify-content: center;
    text-align: center;
    font-family: var(--text-font);
    font-weight: 400;
    text-transform: uppercase;
    letter-spacing: 0.14em;
    line-height: 1.25;
  }
  .card--front .brand-seal {
    left: 230px; top: 80px;
    width: 240px; height: 240px;
    border: 1.5px solid var(--paper);
    color: var(--paper);
    font-size: 26px;
  }
  .card--back .brand-seal {
    left: 460px; top: 22px;
    width: 190px; height: 190px;
    border: 1.5px solid var(--ink);
    color: var(--ink);
    font-size: 20px;
  }

  .card-wave {
    position: absolute;
    inset: 0;
    z-index: 1;
    width: 700px;
    height: 400px;
  }
  .card-wave .wave-silver { fill: var(--silver); }
  .card-wave .wave-ink { fill: var(--ink); }

  .contact {
    position: absolute;
    z-index: 2;
    left: 46px;
    top: 128px;
    color: var(--ink);
  }
  .contact__name {
    font-size: 30px;
    font-weight: 700;
    line-height: 1.1;
  }
  .contact__role {
    font-size: 20px;
    margin: 2px 0 12px 4px;
  }
  .contact__list { list-style: none; }
  .contact__item {
    display: flex;
    align-items: center;
    gap: 6px;
    font-size: 20px;
    line-height: 26px;
    margin-left: 4px;
  }
  .contact__icon {
    width: 14px; height: 14px;
    flex: none;
  }
  .contact__icon--dot { border-radius: 50%; background: var(--ink); }
  .contact__icon--square { border-radius: 2px; background: var(--ink); }
</style>
</head>
<body>
<main class="sheet">

  <section class="card card--front" aria-label="Card front">
    <div class="brand-seal">Rosalind<br>Thorpe<br>Gardens</div>
  </section>

  <section class="card card--back" aria-label="Card back">
    <svg class="card-wave" viewBox="0 0 700 400" aria-hidden="true">
      <path class="wave-silver" d="M0,345 C300,345 520,300 700,190 L700,214 C520,324 300,364 0,364 Z"/>
      <path class="wave-ink" d="M0,364 C300,364 520,324 700,214 L700,400 L0,400 Z"/>
    </svg>

    <div class="brand-seal">Rosalind<br>Thorpe<br>Gardens</div>

    <div class="contact">
      <h1 class="contact__name">Corinne Haldwick</h1>
      <p class="contact__role">Owner</p>
      <ul class="contact__list">
        <li class="contact__item">
          <svg class="contact__icon" viewBox="0 0 16 16" aria-hidden="true">
            <path fill="#0b262b" d="M3.2 1.5l2.4-.4 1.3 3.2-1.6 1.2c.8 1.8 2 3 3.8 3.8l1.2-1.6 3.2 1.3-.4 2.4c-.2 1-1.1 1.7-2.1 1.6C5.8 12.6 2.4 9.2 1.6 3.6c-.1-1 .6-1.9 1.6-2.1z"/>
          </svg>913-555-0147</li>
        <li class="contact__item"><span class="contact__icon contact__icon--dot"></span>RosalindThorpeGardens.example</li>
        <li class="contact__item"><span class="contact__icon contact__icon--square"></span>Rosalind Thorpe Gardens</li>
        <li class="contact__item"><span class="contact__icon contact__icon--square"></span>@RosalindThorpeGardens</li>
      </ul>
    </div>
  </section>

</main>
</body>
</html>
```